Flyer for the Lumen 2025 Conference

I am looking to produce a flyer for our upcoming conference, Lumen 2025. This is an annual conference that we plan to publicize on social media. The ideal designer will create a flyer that is eye-catching and effectively communicates the key information. Please see attached our logo, speaker photo, and flyer content.

Target Market(s)

All demographics

Industry/Entity Type

Christian

Font styles to use
Sans Serif

Requirements
Should not have
• Cross, church

```html
<!DOCTYPE html>
<html lang="en">
<head>
<meta charset="utf-8">
<title>Lumen 2025 Conference Flyer</title>
<link href="https://fonts.googleapis.com/css2?family=Archivo:wght@600;700;800;900&family=Montserrat:wght@400;500;600&family=Allura&display=swap" rel="stylesheet">
<style>
  :root {
    --page-bg: #e6e7e9;
    --navy-deep: #0a2140;
    --navy: #0f3a68;
    --navy-light: #2f5f8f;
    --suit-blue: #2b7bd0;
    --orange: #f39a1e;
    --white: #ffffff;
    --ink: #0b0d12;
    --line: rgba(255,255,255,0.85);
  }
  * { box-sizing: border-box; margin: 0; padding: 0; }
  html, body { width: 1200px; height: 1057px; overflow: hidden; }
  body {
    background: var(--page-bg);
    font-family: "Archivo", Arial, sans-serif;
    position: relative;
  }
  .flyer {
    position: absolute;
    left: 250px; top: 30px;
    width: 700px; height: 997px;
    overflow: hidden;
    background: radial-gradient(ellipse at 30% 35%, var(--navy-light) 0%, var(--navy) 35%, var(--navy-deep) 80%);
    color: var(--white);
  }
  .speaker-photo {
    position: absolute;
    right: 0; top: 0;
    width: 430px; height: 590px;
    background: linear-gradient(160deg, #1d4f86 0%, var(--suit-blue) 45%, rgba(15,58,104,0) 100%);
  }
  .brand-block {
    position: absolute;
    left: 38px; top: 36px;
    width: 190px; height: 190px;
    background: #0d3260;
    display: flex; flex-direction: column; align-items: center; justify-content: center; gap: 6px;
  }
  .brand-name {
    display: flex; align-items: center; gap: 8px;
    font-weight: 800; font-size: 38px; letter-spacing: 1px; color: var(--white);
  }
  .brand-dot { width: 14px; height: 14px; background: var(--orange); border-radius: 50%; }
  .brand-tagline { font-family: "Montserrat", sans-serif; font-size: 9.5px; letter-spacing: 1px; color: var(--orange); text-transform: uppercase; }
  .event-title {
    position: absolute; left: 40px; top: 250px;
    display: flex; gap: 10px; align-items: flex-start;
  }
  .quote-mark { color: var(--orange); font-size: 44px; font-weight: 900; line-height: 0.9; }
  .event-title p { font-weight: 800; font-size: 25px; line-height: 1.15; }
  .topic-frame {
    position: absolute; left: 34px; top: 380px;
    width: 470px; height: 210px;
    border: 2px solid var(--line);
    border-radius: 34px;
  }
  .topic-pill {
    position: absolute; left: 42px; top: 362px;
    background: var(--white); color: var(--navy);
    font-weight: 900; font-size: 24px; letter-spacing: 1px;
    padding: 3px 20px; border-radius: 20px;
  }
  .topic-title {
    position: absolute; left: 62px; top: 400px;
    font-weight: 900; font-size: 72px; line-height: 1.02; color: var(--white);
  }
  .speaker-line {
    position: absolute; left: 52px; top: 606px;
    font-weight: 800; font-size: 31px; color: var(--orange);
  }
  .script-heading {
    font-family: "Allura", cursive; font-weight: 400;
    font-size: 52px; color: var(--white); text-align: center; line-height: 1;
  }
  .schedule-heading { position: absolute; left: 0; right: 0; top: 662px; }
  .schedule {
    position: absolute; left: 30px; right: 30px; top: 722px;
    display: flex; justify-content: space-between;
  }
  .session { display: flex; align-items: center; gap: 8px; }
  .session-day { font-weight: 800; font-size: 21px; }
  .session-rule { width: 2px; height: 34px; background: var(--white); }
  .session-time { font-weight: 700; font-size: 13px; line-height: 1.25; }
  .location-heading { position: absolute; left: 0; right: 0; top: 770px; }
  .venue {
    position: absolute; left: 0; right: 0; top: 826px;
    text-align: center; font-weight: 800; font-size: 15.5px; line-height: 1.35;
  }
  .contact-band {
    position: absolute; left: 0; right: 0; top: 875px;
    height: 95px; background: var(--ink);
    padding: 12px 34px 0;
    font-family: "Montserrat", sans-serif;
  }
  .band-top { display: flex; justify-content: space-between; align-items: center; }
  .app-note { color: var(--orange); font-size: 17px; line-height: 1.1; }
  .store-badges { display: flex; gap: 12px; }
  .store-badge { width: 120px; height: 34px; border: 1.5px solid var(--white); border-radius: 6px; }
  .band-bottom {
    margin-top: 10px; display: flex; align-items: center; gap: 14px;
    font-size: 17px; color: var(--white);
  }
  .band-bottom span { display: flex; align-items: center; gap: 6px; }
  .divider { width: 2px; height: 26px; background: var(--white); }
</style>
</head>
<body>
  <main class="flyer">
    <div class="speaker-photo" role="img" aria-label="Portrait of the speaker seated in a blue suit and glasses"></div>

    <div class="brand-block">
      <div class="brand-name"><span class="brand-dot"></span>AUREL</div>
      <div class="brand-tagline">A Light to Every Nation</div>
    </div>

    <div class="event-title">
      <span class="quote-mark">&rdquo;</span>
      <p>LUMEN 2025<br>A Prophetic Conference</p>
    </div>

    <div class="topic-frame"></div>
    <div class="topic-pill">TOPIC</div>
    <h1 class="topic-title">The Voice<br>Of The Lord</h1>

    <p class="speaker-line">Speaker: Prophet Elias Marren</p>

    <h2 class="script-heading schedule-heading">Date/Time</h2>
    <div class="schedule">
      <div class="session"><span class="session-day">Friday</span><span class="session-rule"></span><span class="session-time">December 26th<br>6:30PM - 9:00PM</span></div>
      <div class="session"><span class="session-day">Saturday</span><span class="session-rule"></span><span class="session-time">December 27th<br>5:30PM - 8:00PM</span></div>
      <div class="session"><span class="session-day">Sunday</span><span class="session-rule"></span><span class="session-time">December 29th<br>4:30PM - 7:00PM</span></div>
    </div>

    <h2 class="script-heading location-heading">Location</h2>
    <p class="venue">The Harbor Hill Performing Arts Center<br>128 Linden Avenue Millbrook, Maine 04010</p>

    <footer class="contact-band">
      <div class="band-top">
        <p class="app-note">Download the Aurel App<br>to stay updated on the event</p>
        <div class="store-badges">
          <span class="store-badge"></span>
          <span class="store-badge"></span>
        </div>
      </div>
      <div class="band-bottom">
        <span>
          <svg width="16" height="16" viewBox="0 0 24 24" aria-hidden="true"><path fill="#f39a1e" d="M6.6 10.8a15.1 15.1 0 0 0 6.6 6.6l2.2-2.2c.3-.3.7-.4 1-.2 1.1.4 2.3.6 3.6.6.6 0 1 .4 1 1V20c0 .6-.4 1-1 1A17 17 0 0 1 3 4c0-.6.4-1 1-1h3.5c.6 0 1 .4 1 1 0 1.3.2 2.5.6 3.6.1.3 0 .7-.2 1z"/></svg>
          207 555 0148
        </span>
        <span class="divider"></span>
        <span>
          <svg width="18" height="14" viewBox="0 0 24 18" aria-hidden="true"><rect x="1" y="1" width="22" height="16" rx="2" fill="none" stroke="#f39a1e" stroke-width="2"/><path d="M1 2l11 8 11-8" fill="none" stroke="#f39a1e" stroke-width="2"/></svg>
          contact@aurelmin.org
        </span>
        <span class="divider"></span>
        <span>
          <svg width="16" height="16" viewBox="0 0 24 24" aria-hidden="true"><circle cx="12" cy="12" r="10" fill="none" stroke="#f39a1e" stroke-width="2"/><path d="M2 12h20M12 2c3 3 3 17 0 20M12 2c-3 3-3 17 0 20" fill="none" stroke="#f39a1e" stroke-width="1.6"/></svg>
          www.aurelmin.org
        </span>
      </div>
    </footer>
  </main>
</body>
</html>
```